New Innovative Counselling and psychotherapy Service needs Business Card design

Keep it simple and professional. On one side, just company name and logo (perhaps in all blue) and maybe a tag line.

On other side (all white) my name and Qualifications in centre

Industry/Entity Type

Health And Wellness

Contact Information for Business Card

Dara Whelby
Counsellor & Psychotherapist
BSc (Psychol.), BA, Dip. (Couns. & Psych.), PG.Cert (CBT), FGTrK, ONRE

I will also require Mobile no, Email and web site address of which I'll pass on to final designer.

Font styles to use
Sans Serif

Requirements
Must have
• My Logo Only and please use the colours in logo that is in it.
Should not have
• Any other images

```html
<!DOCTYPE html>
<html lang="en">
<head>
<meta charset="utf-8">
<title>Kindred Lane – Business Card</title>
<link rel="stylesheet" href="https://fonts.googleapis.com/css2?family=Questrial&family=Roboto:wght@400;700&display=swap">
<style>
  :root {
    --page-bg: #e9e9ea;
    --card-white: #f7f7f7;
    --brand-blue: #45a9e3;
    --brand-teal: #6cc3c4;
    --brand-green: #8fd06a;
    --ink: #2f2f33;
    --ink-soft: #3c3c40;
    --icon-teal: #2aa6a0;
    --icon-green: #6cbf3f;
  }
  * { margin: 0; padding: 0; box-sizing: border-box; }
  html, body { width: 1200px; height: 726px; overflow: hidden; }
  body {
    background: var(--page-bg);
    display: flex;
    align-items: center;
    justify-content: center;
    gap: 44px;
    font-family: "Roboto", Arial, sans-serif;
  }
  .card {
    width: 540px;
    height: 310px;
    border-radius: 4px;
    box-shadow: 0 8px 22px rgba(0,0,0,0.12);
    position: relative;
    overflow: hidden;
  }
  /* Front side */
  .card-front {
    background: linear-gradient(100deg, var(--brand-blue) 0%, var(--brand-teal) 45%, var(--brand-green) 100%);
    display: flex;
    align-items: center;
    justify-content: center;
  }
  .front-wordmark {
    font-family: "Questrial", "Century Gothic", sans-serif;
    font-size: 48px;
    color: #ffffff;
    letter-spacing: 1px;
  }
  /* Back side */
  .card-back {
    background: var(--card-white);
    padding: 44px 40px;
  }
  .brand-lockup {
    display: flex;
    align-items: center;
    gap: 14px;
  }
  .brand-dot {
    width: 46px;
    height: 46px;
    border-radius: 50%;
    background: var(--brand-blue);
    flex: none;
  }
  .brand-name {
    font-family: "Questrial", "Century Gothic", sans-serif;
    font-size: 32px;
    line-height: 0.95;
    color: var(--ink);
  }
  .person { margin-top: 22px; }
  .person-name {
    font-size: 22px;
    font-weight: 700;
    color: var(--brand-blue);
  }
  .person-role {
    font-size: 12px;
    line-height: 1.3;
    color: var(--ink-soft);
    margin-top: 3px;
    max-width: 320px;
  }
  .contact-list {
    list-style: none;
    margin-top: 16px;
    font-size: 14px;
    color: var(--ink);
  }
  .contact-list li {
    display: flex;
    align-items: center;
    gap: 10px;
    line-height: 1.45;
  }
  .contact-icon { width: 13px; height: 13px; flex: none; }
</style>
</head>
<body>
  <section class="card card-front" aria-label="Card front">
    <p class="front-wordmark">Kindred Lane</p>
  </section>

  <section class="card card-back" aria-label="Card back">
    <div class="brand-lockup">
      <span class="brand-dot"></span>
      <p class="brand-name">Kindred<br>Lane</p>
    </div>

    <div class="person">
      <h1 class="person-name">Dara Whelby</h1>
      <p class="person-role">Counsellor &amp; Psychotherapist<br>
        BSc (Psychol.), BA, Dip. (Couns. &amp; Psych.), PG.Cert (CBT), FGTrK, ONRE</p>
    </div>

    <ul class="contact-list">
      <li>
        <svg class="contact-icon" viewBox="0 0 16 16" aria-hidden="true">
          <path fill="var(--icon-teal)" d="M3 2h3l1.5 3.5-2 1.2a8 8 0 0 0 3.8 3.8l1.2-2L14 10v3a1 1 0 0 1-1 1A11 11 0 0 1 2 3a1 1 0 0 1 1-1z"/>
        </svg>
        0161 555 0148
      </li>
      <li>
        <svg class="contact-icon" viewBox="0 0 16 16" aria-hidden="true">
          <rect x="1" y="3" width="14" height="10" rx="1" fill="var(--icon-green)"/>
          <path d="M1.5 3.8 8 9l6.5-5.2" stroke="#fff" stroke-width="1.3" fill="none"/>
        </svg>
        dara.w@KindredLane.com
      </li>
      <li>
        <svg class="contact-icon" viewBox="0 0 16 16" aria-hidden="true">
          <circle cx="8" cy="8" r="7" fill="var(--icon-green)"/>
          <path d="M1 8h14M8 1c-3 3.5-3 10.5 0 14M8 1c3 3.5 3 10.5 0 14" stroke="#fff" stroke-width="1" fill="none"/>
        </svg>
        www.KindredLane.com
      </li>
    </ul>
  </section>
</body>
</html>
```